Business card for my new company (Accounting firm)

I need a business card for my new business Brightwell Advisory and Ledger SA. Our services are accounting, tax, audit and financial management. Our customers are small companies, start-ups and new companies. The final design has to show financial security, trust and growth. Please find our logo attached to the business card. Text for the business card: Brightwell Advisory and Ledger SA Tomas Varenholt Director and Founder Certified Accountant Tel. 022 418 57 34 tv@clairevalconseil.ch www.clairevalconseil.ch Rue des Vergières 27 1201 Geneva
Target Market(s)
Our customers are small companies, start-ups and new companies.
Industry/Entity Type
Finance And Accounting
Contact Information for Business Card
Claireval Conseil et Comptes SA
Tomas Varenholt
Directeur et Fondateur
Expert-comptable diplômé
Tél. 022 418 57 34
tv@clairevalconseil.ch
www.clairevalconseil.ch
Rue des Vergières 27
1201 Genève

```html
<!DOCTYPE html>
<html lang="fr">
<head>
<meta charset="utf-8">
<title>Claireval Conseil et Comptes SA – Carte de visite</title>
<link rel="stylesheet" href="https://fonts.googleapis.com/css2?family=Roboto:wght@400;500;700&display=swap">
<style>
  :root {
    --page-bg: #e6e4e0;
    --card-frost: #eeeeec;
    --blue-deep: #1c6598;
    --blue-light: #2c8cc2;
    --curve-shadow: #3a3d42;
    --text-light: #f4f1ec;
    --text-soft: #e4e9ee;
    --brand-ink: #3b4046;
  }
  * { box-sizing: border-box; margin: 0; padding: 0; }
  html, body {
    width: 1200px; height: 1054px; overflow: hidden;
    background: var(--page-bg);
    font-family: "Roboto", Arial, sans-serif;
  }
  .business-card {
    position: absolute; left: 100px; top: 225px;
    width: 1000px; height: 604px;
    background: var(--card-frost);
    box-shadow: 0 10px 30px rgba(0,0,0,.15);
    overflow: hidden;
  }
  .card-band { position: absolute; inset: 0; width: 100%; height: 100%; }
  .identity { position: absolute; left: 53px; top: 100px; color: var(--text-light); }
  .identity__name { font-size: 38px; font-weight: 700; letter-spacing: .2px; margin-bottom: 14px; }
  .identity__role { font-size: 23px; font-weight: 400; line-height: 31px; color: var(--text-soft); }
  .contact { position: absolute; left: 53px; top: 356px; color: var(--text-soft); font-size: 23px; }
  .contact__address { line-height: 37px; margin-bottom: 8px; }
  .contact__row { display: flex; align-items: center; height: 38px; }
  .contact__icon { width: 24px; height: 24px; margin-right: 23px; fill: var(--text-soft); }
  .brand {
    position: absolute; left: 600px; width: 354px; top: 300px;
    text-align: center; color: var(--brand-ink); font-weight: 500;
  }
  .brand__name { font-size: 64px; letter-spacing: 4px; line-height: 1; text-transform: uppercase; }
  .brand__line { font-size: 21px; letter-spacing: 3px; margin-top: 12px; text-transform: uppercase; }
</style>
</head>
<body>
<main class="business-card">
  <svg class="card-band" viewBox="0 0 1000 604" aria-hidden="true">
    <defs>
      <linearGradient id="band-blue" x1="0" y1="0" x2="1" y2="1">
        <stop offset="0" stop-color="var(--blue-deep)"/>
        <stop offset="1" stop-color="var(--blue-light)"/>
      </linearGradient>
    </defs>
    <path d="M0 0 H608 C 525 140, 500 430, 598 604 H0 Z" fill="var(--curve-shadow)"/>
    <path d="M0 0 H590 C 505 140, 482 430, 582 604 H0 Z" fill="url(#band-blue)"/>
  </svg>

  <section class="identity">
    <h1 class="identity__name">Tomas Varenholt</h1>
    <p class="identity__role">Directeur et Fondateur</p>
    <p class="identity__role">Expert-comptable diplômé</p>
  </section>

  <section class="contact">
    <p class="contact__address">Rue des Vergières 27<br>1201 Genève</p>
    <p class="contact__row">
      <svg class="contact__icon" viewBox="0 0 24 24" aria-hidden="true"><path d="M3 9c0-2 4-4 9-4s9 2 9 4v2h-4V9.5c-1.5-.6-3-.8-5-.8s-3.5.2-5 .8V11H3z M7 12h10l2 7H5z"/></svg>
      022 418 57 34
    </p>
    <p class="contact__row">
      <svg class="contact__icon" viewBox="0 0 24 24" aria-hidden="true"><path d="M3 6h18v12H3z M4.5 7.5v.3l7.5 5 7.5-5v-.3z" fill-rule="evenodd"/></svg>
      tv@clairevalconseil.ch
    </p>
    <p class="contact__row">
      <svg class="contact__icon" viewBox="0 0 24 24" aria-hidden="true"><circle cx="12" cy="12" r="8"/><path d="M4 12h16M12 4c-3 3-3 13 0 16M12 4c3 3 3 13 0 16" stroke="var(--blue-deep)" stroke-width="1.2" fill="none"/></svg>
      www.clairevalconseil.ch
    </p>
  </section>

  <section class="brand">
    <p class="brand__name">Claireval</p>
    <p class="brand__line">Conseil et Comptes SA</p>
  </section>
</main>
</body>
</html>
```